QZSTREAMHUB ( Wordpress website for catalogue of Vorlo Stream Pages)

Need a website to showcase different Vorlo Stream pages ( in different categories). Similar to e-commerce except no check-out / purchase of items. Pls use our logos provided and color scheme to be white+red+ blue as per our logo.

Target Market(s)

Consumers

Font styles to use
Sans Serif

Colors
ffffff
ec1f27
3276b5

Requirements
Must have
• I will need a Wordpress Theme as a handover. Also, pls use the color scheme (red+blue+white) as per logo attached. Prefer clean and near design with white space.

```html
<!DOCTYPE html>
<html lang="en">
<head>
<meta charset="utf-8">
<title>QZSTREAMHUB – Vorlo Stream Pages</title>
<link href="https://fonts.googleapis.com/css2?family=Anton&family=Dancing+Script:wght@700&family=Roboto:wght@400;500;700&family=Roboto+Slab:wght@700&display=swap" rel="stylesheet">
<style>
:root{
  --red:#ec1f27;
  --blue:#3276b5;
  --blue-deep:#2b5da6;
  --navy:#1c3a70;
  --white:#ffffff;
  --ink:#222222;
  --text:#333333;
  --icon:#4a4a4a;
  --pale:#eef2fb;
  --maroon:#5e0812;
  --footer:#1c1f2c;
}
*{margin:0;padding:0;box-sizing:border-box}
html,body{width:1200px;height:3725px;overflow:hidden}
body{font-family:'Roboto',sans-serif;color:var(--text);background:var(--white);position:relative}
section,header,footer{position:relative;width:1200px;overflow:hidden}
.btn{display:inline-block;background:var(--red);color:var(--white);font-size:14px;text-align:center;text-decoration:none;border-radius:2px;position:absolute}

/* header */
.site-header{height:84px;background:var(--white)}
.brand{position:absolute;left:145px;top:19px;display:flex;align-items:center;gap:10px}
.brand-mark{width:22px;height:22px;background:var(--red)}
.brand-name{font-weight:700;font-size:36px;color:var(--blue-deep);letter-spacing:-0.5px}
.main-nav{position:absolute;left:496px;top:32px;display:flex;gap:40px;font-size:15px;color:var(--ink)}
.main-nav .active{color:var(--blue-deep)}
.site-header .btn{left:947px;top:25px;width:108px;height:36px;line-height:36px;font-size:15px}

/* hero */
.hero{height:516px;background:var(--pale)}
.hero-shapes{position:absolute;left:0;top:0}
.hero-title{position:absolute;left:145px;top:146px;font-family:'Anton',sans-serif;font-size:64px;line-height:54px;color:var(--ink);letter-spacing:-1px}
.hero-title .script{font-family:'Dancing Script',cursive;color:var(--red);font-size:62px;letter-spacing:0}
.hero-title .live{display:inline-block;margin-top:8px;background:var(--red);color:var(--white);font-size:50px;line-height:50px;padding:0 8px;border:3px solid var(--white);outline:2px solid var(--red)}
.hero-art{position:absolute;left:452px;top:104px;width:740px;height:318px;border-radius:24px;background:linear-gradient(100deg,#dfe6f4 0%,#f1d3d9 35%,#e8b9a4 60%,#cfdcf4 100%)}
.hero-arrow{position:absolute;top:244px;width:40px;height:40px;border-radius:50%;background:#1e2230}
.hero-arrow.prev{left:55px}.hero-arrow.next{left:1103px}
.hero-arrow svg{position:absolute;left:13px;top:11px}
.hero-bar{height:14px;background:linear-gradient(90deg,var(--red) 0 46%,var(--blue-deep) 46% 100%)}

/* welcome */
.welcome{height:698px}
.welcome-art{position:absolute;left:137px;top:66px;width:441px;height:549px;border-radius:8px;background:radial-gradient(circle at 50% 60%,#3e62e2 0 44%,#e9eefa 45%)}
.welcome h2{position:absolute;left:640px;top:170px;font-size:40px;font-weight:500;color:var(--blue-deep)}
.welcome p{position:absolute;left:641px;top:236px;width:418px;font-size:14.5px;line-height:32px;color:var(--text)}
.welcome .btn{left:641px;top:482px;width:112px;height:39px;line-height:39px}

/* categories */
.categories{height:413px;background:linear-gradient(90deg,var(--maroon),#b0041c)}
.section-title{position:absolute;left:0;width:1200px;text-align:center;font-size:40px;font-weight:500}
.categories .section-title{top:68px;color:var(--white)}
.cat-list{position:absolute;top:139px;left:145px;display:flex;gap:29px}
.cat-item{width:159px;text-align:center;color:var(--white);font-size:19px}
.cat-circle{width:159px;height:159px;border-radius:50%;background:var(--white);display:flex;align-items:center;justify-content:center;margin-bottom:16px}
.cat-circle svg{width:90px;height:90px}
.cat-circle svg *{fill:none;stroke:var(--icon);stroke-width:3;stroke-linejoin:round;stroke-linecap:round}
.cat-arrow{position:absolute;top:207px}
.cat-arrow.prev{left:54px}.cat-arrow.next{left:1125px}

/* live pages */
.live-pages{height:647px}
.live-pages .section-title{top:72px;color:var(--blue-deep)}
.page-grid{position:absolute;left:145px;top:148px;display:grid;grid-template-columns:repeat(5,162px);column-gap:25px;row-gap:31px}
.page-card{height:161px;border:1px solid #c9c9c9;background:#fbf8f1;position:relative;overflow:hidden}
.card-label{position:absolute;left:6px;top:7px;font-size:11px;font-weight:700;color:var(--red)}
.card-price{position:absolute;right:7px;top:6px;width:84px;text-align:right;font-family:'Roboto Slab',serif;font-size:14px;font-weight:700;color:var(--ink);line-height:15px}
.card-price small{display:block;font-family:'Roboto',sans-serif;font-weight:400;font-size:7px;color:#555;line-height:10px}
.card-photo{position:absolute;left:0;top:38px;width:100%;height:80px;background:linear-gradient(160deg,#f3d9b8,#d9773e 50%,#9b2a22)}
.card-photo.satay{background:linear-gradient(160deg,#f0d39a,#c98a2a 50%,#6b2c14)}
.card-photo.milk{background:linear-gradient(160deg,#e8f0fb,#9bbbe2 50%,#e9e2d2)}
.card-photo.mask{background:radial-gradient(circle at 45% 55%,#1d1d1d 0 32%,#f6f2ea 34%)}
.card-brand{position:absolute;left:0;bottom:18px;width:100%;text-align:center;font-family:'Roboto Slab',serif;font-size:11px;font-weight:700;color:var(--ink)}
.card-note{position:absolute;left:0;bottom:7px;width:100%;text-align:center;font-size:7.5px;color:#333}
.card-dot{position:absolute;right:5px;bottom:5px;width:14px;height:14px;border-radius:50%;background:#1b1b1b}
.live-pages .btn{left:548px;top:528px;width:104px;height:39px;line-height:39px}

/* reviews */
.reviews{height:559px;background:linear-gradient(135deg,#1d3b72,#2b62ad)}
.reviews .section-title{top:78px;color:var(--white)}
.review-list{position:absolute;left:145px;top:132px;display:flex;gap:21px}
.review{width:290px;height:281px;border:1px solid rgba(255,255,255,.85);padding:22px 22px;color:var(--white)}
.review .quote{font-family:Georgia,serif;font-size:50px;line-height:40px;font-weight:700;height:34px}
.review p{font-size:14.5px;line-height:26px;margin-top:6px;height:134px}
.review .name{font-size:17px;font-weight:500;margin-top:4px}
.review .stars{font-size:15px;letter-spacing:2px}
.reviews .btn{left:548px;top:439px;width:104px;height:39px;line-height:39px}

/* stats */
.stats{height:250px}
.stat{position:absolute;top:72px;width:300px;text-align:center}
.stat .num{font-size:56px;font-weight:500;color:var(--blue-deep);line-height:64px}
.stat .label{font-size:23px;color:var(--ink);font-weight:500}

/* contact */
.contact{height:431px;background:var(--pale)}
.contact .section-title{top:70px;color:var(--blue-deep)}
.field{position:absolute;background:var(--white);border:1px solid #c9c9c9;font-size:13px;color:#8a8a8a;padding:12px 15px}
.field.sm{top:133px;width:298px;height:38px;padding-top:11px}
.field.msg{left:145px;top:185px;width:910px;height:102px}
.contact .btn{left:548px;top:312px;width:104px;height:39px;line-height:39px}

/* footer */
.site-footer{height:113px;background:var(--footer);color:#d6d6d6;font-size:11px}
.footer-links{position:absolute;left:145px;top:34px}
.copyright{position:absolute;left:145px;top:66px}
.social{position:absolute;left:946px;top:36px;display:flex;gap:26px}
.social span{width:18px;height:18px;border-radius:50%;background:#c8d4e8}
</style>
</head>
<body>

<header class="site-header">
  <div class="brand"><span class="brand-name">QZSTREAMHUB</span><span class="brand-mark"></span></div>
  <nav class="main-nav">
    <span class="active">Categories</span><span>Live Pages</span><span>About Us</span><span>Contact Us</span>
  </nav>
  <a class="btn">Get Started</a>
</header>

<section class="hero">
  <svg class="hero-shapes" width="1200" height="516" viewBox="0 0 1200 516" aria-hidden="true">
    <defs>
      <linearGradient id="blobL" x1="0" y1="0" x2="1" y2="1"><stop offset="0" stop-color="#8a5bb5"/><stop offset="1" stop-color="#e58ac0"/></linearGradient>
      <linearGradient id="blobR" x1="0" y1="0" x2="1" y2="1"><stop offset="0" stop-color="#c7d7f5"/><stop offset="1" stop-color="#4d6fd6"/></linearGradient>
    </defs>
    <path d="M0 0 H170 C150 60 90 80 40 110 C20 122 8 140 0 150 Z" fill="url(#blobL)"/>
    <path d="M1115 0 H1200 V62 C1168 52 1138 30 1115 0 Z" fill="url(#blobR)"/>
  </svg>
  <div class="hero-title">A PORTAL <span class="script">of</span><br>CURATED<br>VORLO<br><span class="live">LIVE</span></div>
  <div class="hero-art" role="img" aria-label="Illustration of a smartphone showing a live stream shop, with two shoppers holding bags and boxes among groceries and clothing racks"></div>
  <div class="hero-arrow prev"><svg width="14" height="18" viewBox="0 0 14 18"><path d="M10 2 L3 9 L10 16" stroke="#fff" stroke-width="3" fill="none"/></svg></div>
  <div class="hero-arrow next"><svg width="14" height="18" viewBox="0 0 14 18"><path d="M4 2 L11 9 L4 16" stroke="#fff" stroke-width="3" fill="none"/></svg></div>
</section>
<div class="hero-bar"></div>

<section class="welcome">
  <div class="welcome-art" role="img" aria-label="Illustration of a person sitting on a desk with a laptop above a dashboard with bar charts"></div>
  <h2>Welcome to QZ Stream Hub</h2>
  <p>Fusce nec leo urna pulvinar auctor. Mauris bibendum fringilla velit. Nulla in lorem at massa pellentesque posuere. Nulla tristique posuere molestie. Aliquam erat volutpat. Etiam quis aliquet risus. Duis ornare eget magna dapibus, in accumsan quam pharetra. Nam tempus, quam in bibendum vulputate, sapien dolor viverra nisl, vitae euismod elit turpis et nulla blandit lacus eget nunc.</p>
  <a class="btn">READ MORE</a>
</section>

<section class="categories">
  <h2 class="section-title">Categories</h2>
  <svg class="cat-arrow prev" width="18" height="28" viewBox="0 0 18 28"><path d="M14 3 L4 14 L14 25" stroke="#fff" stroke-width="3.5" fill="none"/></svg>
  <div class="cat-list">
    <div class="cat-item"><div class="cat-circle">
      <svg viewBox="0 0 90 90" role="img" aria-label="Meat icon"><path d="M10 40 h24 l18 -14 h6 a16 16 0 0 1 0 34 h-6 l-18 -10 h-24 z"/><ellipse cx="62" cy="43" rx="8" ry="12"/><ellipse cx="62" cy="43" rx="3" ry="5"/><circle cx="10" cy="36" r="4"/><circle cx="10" cy="48" r="4"/></svg>
    </div>Meat</div>
    <div class="cat-item"><div class="cat-circle">
      <svg viewBox="0 0 90 90" role="img" aria-label="Milk carton icon"><rect x="32" y="10" width="26" height="8"/><path d="M30 18 h30 l8 14 v48 h-46 v-48 z"/><path d="M22 32 h46"/><path d="M45 44 c-6 8 -8 12 -8 16 a8 8 0 0 0 16 0 c0 -4 -2 -8 -8 -16 z"/></svg>
    </div>Milk</div>
    <div class="cat-item"><div class="cat-circle">
      <svg viewBox="0 0 90 90" role="img" aria-label="Face mask icon"><path d="M28 30 l28 -14 l16 22 l-28 30 l-26 -16 z"/><path d="M34 36 l24 -12 M36 46 l26 -14 M40 56 l26 -16"/><circle cx="18" cy="62" r="7"/><circle cx="70" cy="18" r="7"/></svg>
    </div>Face Masks</div>
    <div class="cat-item"><div class="cat-circle">
      <svg viewBox="0 0 90 90" role="img" aria-label="Vegetables icon"><rect x="24" y="10" width="10" height="8"/><path d="M22 18 h14 v16 h-14 z"/><circle cx="44" cy="44" r="11"/><circle cx="58" cy="48" r="9"/><path d="M14 72 l50 -8 l8 8 l-8 6 z"/><path d="M72 72 l8 -6 M72 72 l9 4"/><path d="M28 62 a8 8 0 1 1 12 -6"/></svg>
    </div>Vegetables</div>
    <div class="cat-item"><div class="cat-circle">
      <svg viewBox="0 0 90 90" role="img" aria-label="Food containers icon"><rect x="14" y="36" width="62" height="26" rx="3"/><path d="M18 36 v-16 h20 v16 M52 36 v-20 h22 v20"/><ellipse cx="28" cy="20" rx="10" ry="4"/><ellipse cx="63" cy="16" rx="11" ry="4"/><path d="M10 70 h70 M22 62 v8 M68 62 v8"/><rect x="38" y="42" width="14" height="14"/></svg>
    </div>Food Items</div>
  </div>
  <svg class="cat-arrow next" width="18" height="28" viewBox="0 0 18 28"><path d="M4 3 L14 14 L4 25" stroke="#fff" stroke-width="3.5" fill="none"/></svg>
</section>

<section class="live-pages">
  <h2 class="section-title">Our Live Pages</h2>
  <div class="page-grid">
    <div class="page-card"><span class="card-label">Combo A</span><div class="card-price">$40/-<small>With Delivery</small></div><div class="card-photo" role="img" aria-label="Photo of a meat combo pack"></div><div class="card-brand">ShopNook</div><div class="card-note">Order online today</div><span class="card-dot"></span></div>
    <div class="page-card"><span class="card-label">Combo B</span><div class="card-price">$40/-<small>With Delivery</small></div><div class="card-photo satay" role="img" aria-label="Photo of a meat combo pack"></div><div class="card-brand">ShopNook</div><div class="card-note">Order online today</div><span class="card-dot"></span></div>
    <div class="page-card"><span class="card-label">Combo C</span><div class="card-price">$40/-<small>With Delivery</small></div><div class="card-photo" role="img" aria-label="Photo of a meat combo pack"></div><div class="card-brand">ShopNook</div><div class="card-note">Order online today</div><span class="card-dot"></span></div>
    <div class="page-card"><span class="card-label">Satay Offer</span><div class="card-price">$28/- only<small>25 Sticks</small></div><div class="card-photo satay" role="img" aria-label="Photo of satay skewers"></div><div class="card-brand">ShopNook</div><div class="card-note">Order online today</div><span class="card-dot"></span></div>
    <div class="page-card"><span class="card-label">Milk Offer</span><div class="card-price">Buy 2 for $5.55</div><div class="card-photo milk" role="img" aria-label="Photo of milk cartons"></div><div class="card-brand">ShopNook</div><div class="card-note">Order online today</div><span class="card-dot"></span></div>
    <div class="page-card"><span class="card-label">New</span><div class="card-price" style="font-size:9px;line-height:11px">Purchase during our Live today</div><div class="card-photo mask" role="img" aria-label="Photo of a black face mask"></div><div class="card-brand">ShopNook</div><div class="card-note">Order online today</div><span class="card-dot"></span></div>
    <div class="page-card"><span class="card-label">New</span><div class="card-price">$10.95 only<small>25 Sticks</small></div><div class="card-photo" role="img" aria-label="Photo of beef satay skewers"></div><div class="card-brand">ShopNook</div><div class="card-note">Order online today</div><span class="card-dot"></span></div>
    <div class="page-card"><span class="card-label">New</span><div class="card-price">$9.95 only<small>25 Sticks</small></div><div class="card-photo satay" role="img" aria-label="Photo of chicken satay skewers"></div><div class="card-brand">ShopNook</div><div class="card-note">Order online today</div><span class="card-dot"></span></div>
    <div class="page-card"><span class="card-label">New</span><div class="card-price">$12.45 only<small>25 Sticks</small></div><div class="card-photo" role="img" aria-label="Photo of mutton satay skewers"></div><div class="card-brand">ShopNook</div><div class="card-note">Order online today</div><span class="card-dot"></span></div>
    <div class="page-card"><span class="card-label">Combo B</span><div class="card-price">$40/-<small>With Delivery</small></div><div class="card-photo satay" role="img" aria-label="Photo of a meat combo pack"></div><div class="card-brand">ShopNook</div><div class="card-note">Order online today</div><span class="card-dot"></span></div>
  </div>
  <a class="btn">VIEW ALL</a>
</section>

<section class="reviews">
  <h2 class="section-title">Reviews</h2>
  <div class="review-list">
    <div class="review"><div class="quote">“</div><p>Phasellus nisl condimentum vitae faucibus sollicitudin vel metus. Nunc amet consequat risus. Curabitur ac elit leo. In eleifend tellus, in scelerisque elit porttitor</p><div class="name">SOPHIA, NEW YORK</div><div class="stars">★★★★★</div></div>
    <div class="review"><div class="quote">“</div><p>Nulla diam purus, ultrices sed metus sed, bibendum malesuada neque. Vivamus hendrerit maximus tempus. Integer porta erat at nulla posuere fringilla.</p><div class="name">EMMA, NEW YORK</div><div class="stars">★★★★★</div></div>
    <div class="review"><div class="quote">“</div><p>Sed consectetur sed elit sit amet sodales. Donec vestibulum tris tique orci aliquet lorem commodo eu. Integer tellus, tempus sit amet nisi rhoncus feugiat.</p><div class="name">MADISON, NEW YORK</div><div class="stars">★★★★★</div></div>
  </div>
  <a class="btn">VIEW ALL</a>
</section>

<section class="stats">
  <div class="stat" style="left:139px"><div class="num">38,592</div><div class="label">Fusce eget</div></div>
  <div class="stat" style="left:450px"><div class="num">12.86</div><div class="label">Maecenas</div></div>
  <div class="stat" style="left:761px"><div class="num">182</div><div class="label">Pellentesque</div></div>
</section>

<section class="contact">
  <h2 class="section-title">Contact Us</h2>
  <div class="field sm" style="left:145px">Name</div>
  <div class="field sm" style="left:451px">Email</div>
  <div class="field sm" style="left:757px">Title</div>
  <div class="field msg">Message</div>
  <a class="btn">SUBMIT</a>
</section>

<footer class="site-footer">
  <div class="footer-links">Home &nbsp;|&nbsp; Categories &nbsp;|&nbsp; Live Pages &nbsp;|&nbsp; About Us &nbsp;|&nbsp; Contact Us &nbsp;|&nbsp; Get Started</div>
  <div class="copyright">Copyright © 2020 QZSTREAMHUB. All rights reserved.</div>
  <div class="social" aria-label="Social links"><span></span><span></span><span></span></div>
</footer>

</body>
</html>
```